Maple Beacon Website

We are starting a marketing company and to do that we need a website! We want a website that will inspire and persuade to bring out the awesomeness in our clients.
What we want to see:
- Inspirational and persuasive imagery that relate to Branding.
- No cliche images eg. business man, suits and hand shakes
- We want to transform and educate our clients.
- We want to show them the path and would like our website to really act as a guide that guides them step by step through our process.
- We want the portray that we are an investment but not have a pretentious way to it. We put our heart into every project and that is how we treat our clients.
-When you submit your design please include what platform you have created for. Preference would be Wordpress or Joobla.

We have included the psd file for the wire frame, logo files, font files, site map and a link to a video we create to give you more information on what we would like to see. http://clipvault.example/t/qk82LmZpr

Feel free to make small modification to the logos if you think it will improve it. Your creativity and advice is most welcome.
Updates

One thing we forgot. We would like to have our contact information near the top of the website as well as at the bottom.  Here is out contact info:

Email: info@maplebeacon.example
Phone: 587-555-0142

Project Deadline Extended
Reason: As we are new with the platform and that we want to optimize our results, we decided to extend the deadline by 15 days. Thanks!

Target Market(s)

28-60, Male and Female, Oil field, Local Businesses, Dentists, Chiropractors, Hair salon, Construction/Renovation, Events etc

Industry/Entity Type

Investment

Requirements
Must have
• - 4 Inspirational and persuasive Imagery for the top portion of the website
- Must have a feel as if your not on a website an example of this is linked below.
http://www.artbidhub.example/design/402957/web-design-by-lena-torvik
Nice to have
• - Creative advice from you.
- Creative buttons for Get Free Quote and Subscribe buttons. Something out of the box that draws peoples attention. eg. a 'B' button. Just and example but still something related to branding.
Should not have
• No Cliches

```html
<!DOCTYPE html>
<html lang="en">
<head>
<meta charset="utf-8">
<title>Maple Beacon</title>
<link rel="stylesheet" href="https://fonts.googleapis.com/css2?family=Source+Sans+3:ital,wght@0,300;0,400;0,600;0,700;1,600&family=Cabin:wght@700&display=swap">
<style>
  :root {
    --leaf-dark: #4b6b1f;
    --leaf: #7a9c24;
    --lime: #b4d535;
    --band: #a6c552;
    --ink: #222;
    --body-text: #6a6a6a;
    --steel-top: #6b7586;
    --steel-bottom: #2f353e;
    --rule: #cfcfcf;
  }
  * { box-sizing: border-box; margin: 0; padding: 0; }
  html, body { width: 1200px; height: 792px; overflow: hidden; }
  body {
    position: relative;
    font-family: "Source Sans 3", "Myriad Pro", sans-serif;
    background: #fff;
    color: var(--ink);
  }
  .top-rule { position: absolute; left: 0; top: 0; width: 1200px; height: 4px; background: var(--leaf-dark); }
  .masthead {
    position: absolute; left: 0; top: 4px; width: 1200px; height: 376px;
    background: linear-gradient(#ffffff, #e4e4e4);
  }
  .sidebar {
    position: absolute; left: 101px; top: 4px; width: 255px; height: 376px;
    background: #fff; border-left: 1px solid var(--rule); border-right: 1px solid var(--rule);
  }
  .brand {
    position: absolute; left: 14px; top: 18px; display: flex; align-items: center; gap: 8px;
  }
  .brand-dot { width: 22px; height: 22px; border-radius: 50%; background: #8b8b8b; }
  .brand-name { font-size: 31px; font-weight: 700; color: #8b8b8b; letter-spacing: 0.5px; }
  .tagline {
    position: absolute; left: 0; top: 82px; width: 253px; text-align: center;
    font-size: 14px; font-weight: 600; font-style: italic; color: #555;
  }
  .side-nav { position: absolute; left: 22px; top: 128px; list-style: none; }
  .side-nav li {
    display: flex; align-items: center; gap: 10px; height: 40px;
    font-size: 14px; font-weight: 700; text-transform: uppercase; color: var(--ink);
  }
  .side-nav li.current { color: var(--leaf-dark); }
  .side-nav svg { width: 18px; height: 12px; }

  .main-nav { position: absolute; left: 598px; top: 4px; display: flex; height: 53px; }
  .main-nav a {
    display: flex; align-items: center; padding: 0 14px; font-size: 18px; color: #333; text-decoration: none;
  }
  .main-nav a.current { background: var(--lime); color: #3b4c12; }
  .main-nav a.found { padding: 0 21px; }
  .main-nav a.connect { padding: 0 17px; }

  .hero {
    position: absolute; left: 369px; top: 57px; width: 702px; height: 316px;
    border: 4px solid var(--lime);
  }
  .hero-image {
    position: absolute; inset: 0;
    background: radial-gradient(ellipse at 25% 15%, #f4faee 0%, #d5ecb6 30%, #9fd04a 60%, #5e9e15 100%);
  }
  .hero-title {
    position: absolute; right: 34px; top: 50px;
    font-family: "Cabin", sans-serif; font-weight: 700; font-size: 40px; color: var(--leaf-dark); letter-spacing: 0.5px;
  }
  .hero-dots { position: absolute; left: 23px; bottom: 10px; display: flex; gap: 9px; }
  .hero-dots span { width: 13px; height: 13px; border-radius: 50%; background: #fff; }

  .newsletter { position: absolute; left: 0; top: 380px; width: 1200px; height: 70px; background: var(--band); }
  .connect-label {
    position: absolute; left: 108px; top: 18px; font-size: 15px; font-weight: 700; line-height: 16px; color: var(--leaf-dark);
  }
  .social { position: absolute; left: 185px; top: 21px; display: flex; gap: 5px; }
  .social span { width: 27px; height: 27px; border-radius: 50%; background: #fff; }
  .social span:first-child { background: #5a7a1f; }
  .newsletter-pitch {
    position: absolute; left: 362px; top: 23px; font-size: 18px; font-weight: 700; color: #fff;
  }
  .email-field {
    position: absolute; left: 782px; top: 19px; width: 182px; height: 34px; background: #eeeeee;
    padding-left: 12px; display: flex; align-items: center; font-size: 14px; color: #777;
  }
  .button-dark {
    display: flex; align-items: center; justify-content: center;
    background: linear-gradient(#5e6776, #333a44); color: #fff; font-weight: 600; border-radius: 2px;
  }
  .subscribe { position: absolute; left: 973px; top: 19px; width: 97px; height: 34px; font-size: 17px; }

  .content {
    position: absolute; left: 0; top: 450px; width: 1200px; height: 260px;
    background: linear-gradient(#ffffff, #e3e3e3);
  }
  .welcome { position: absolute; left: 191px; top: 26px; width: 522px; }
  .section-title { font-size: 22px; font-weight: 700; color: var(--leaf); line-height: 28px; }
  .welcome .section-title { border-bottom: 1px solid #8aa832; padding-bottom: 3px; margin-bottom: 18px; }
  .welcome p {
    font-size: 14.5px; font-weight: 300; line-height: 18px; color: var(--body-text);
    text-align: justify; margin-bottom: 18px; padding-left: 1px;
  }
  .quote { position: absolute; left: 743px; top: 26px; width: 265px; }
  .quote .section-title { font-size: 18px; line-height: 24px; margin-bottom: 4px; }
  .quote p { font-size: 13.5px; line-height: 22px; color: #444; margin-bottom: 14px; }
  .quote-button { width: 138px; height: 34px; font-size: 16px; }

  .footer {
    position: absolute; left: 0; top: 710px; width: 1200px; height: 82px;
    border-top: 2px solid var(--leaf); background: linear-gradient(var(--steel-top), var(--steel-bottom));
    color: #fff; text-align: center;
  }
  .footer-links { margin-top: 19px; font-size: 14px; }
  .footer-links span { margin: 0 6px; }
  .copyright { margin-top: 12px; font-size: 14px; }
</style>
</head>
<body>
  <div class="top-rule"></div>
  <header class="masthead">
    <aside class="sidebar">
      <div class="brand"><span class="brand-dot"></span><span class="brand-name">Maple Beacon</span></div>
      <p class="tagline">Because You´re Awesome!</p>
      <ul class="side-nav">
        <li class="current"><svg viewBox="0 0 18 12"><ellipse cx="9" cy="6" rx="8" ry="4.5" fill="#6f9a2a" transform="rotate(-15 9 6)"/></svg>Strategy</li>
        <li><svg viewBox="0 0 18 12"><ellipse cx="9" cy="6" rx="8" ry="4.5" fill="#6f9a2a" transform="rotate(-15 9 6)"/></svg>Portfolio</li>
        <li><svg viewBox="0 0 18 12"><ellipse cx="9" cy="6" rx="8" ry="4.5" fill="#6f9a2a" transform="rotate(-15 9 6)"/></svg>About Us</li>
        <li><svg viewBox="0 0 18 12"><ellipse cx="9" cy="6" rx="8" ry="4.5" fill="#6f9a2a" transform="rotate(-15 9 6)"/></svg>Contact Us</li>
        <li><svg viewBox="0 0 18 12"><ellipse cx="9" cy="6" rx="8" ry="4.5" fill="#6f9a2a" transform="rotate(-15 9 6)"/></svg>Blog</li>
      </ul>
    </aside>
    <nav class="main-nav">
      <a class="current">Maple Beacon</a>
      <a class="found">Be Found</a>
      <a class="connect">Connect</a>
      <a>Get Growing</a>
    </nav>
  </header>

  <section class="hero">
    <div class="hero-image" role="img" aria-label="Close-up of fresh green grass blades in soft morning light"></div>
    <h1 class="hero-title">MAPLE BEACON</h1>
    <div class="hero-dots"><span></span><span></span><span></span><span></span></div>
  </section>

  <section class="newsletter">
    <p class="connect-label">Connect<br>with us !</p>
    <div class="social"><span></span><span></span><span></span><span></span><span></span></div>
    <p class="newsletter-pitch">Get Tips and Tricks! Subscribe to our Newsletter.</p>
    <div class="email-field">Enter your email id</div>
    <div class="button-dark subscribe">Subscribe</div>
  </section>

  <main class="content">
    <div class="welcome">
      <h2 class="section-title">WELCOME!</h2>
      <p>Lorem ipsum dolor sit amet, consectetur adipisicing elit, sed do eiusmod tempor incididunt ut labore et dolore magna aliqua. Ut enim ad minim veniam, quis nostrud exercitation ullamco laboris nisi ut aliquip ex ea commodo consequat. Duis aute irure dolor in reprehenderit in voluptate velit esse cillum dolore eu fugiat nulla pariatur. Excepteur sint occaecat cupidatat non proident, sunt in culpa qui officia deseruntilil</p>
      <p>Sed ut perspiciatis unde omnis iste natus error sit voluptatem accusantium doloremque laudantium,</p>
    </div>
    <div class="quote">
      <h2 class="section-title">GET A QUOTE NOW</h2>
      <p>Lamcorper nonummy, nibh ligula pulvinar metus, eget consectetuer augue nisi quis lacus. Ut ac mi quis lacus mo</p>
      <div class="button-dark quote-button">Get a Free Quote</div>
    </div>
  </main>

  <footer class="footer">
    <p class="footer-links">Site Map<span>|</span>Strategy<span>|</span>Portfolio<span>|</span>About Us<span>|</span>Contact Us<span>|</span>Blog</p>
    <p class="copyright">© MAPLE BEACON INC. 2013</p>
  </footer>
</body>
</html>
```